Catalogue Design Project

We need a catalog design for a new private university called Redwell Institute Bayshore (see website www.rwi-bs.org). The catalog should be about 30 pages maximum and will include items such as General Information, Academic schedule, department descriptions, program descriptions, course descriptions, school policies, student services, admissions, San diego Lifestyle, etc.
I will provide the text but I need a professional design with regard to page layouts. I have provided some examples.
Ok, i posted the catalog content, just missing course descriptions.
Target Market(s)
Young Professionals, Foreign Students
Industry/Entity Type
University
Look and feel
Each slider illustrates characteristics of the customer's brand and the style your logo design should communicate.

```html
<!DOCTYPE html>
<html lang="en">
<head>
<meta charset="utf-8">
<title>Graduation Requirements – Redwell Institute Bayshore Catalogue</title>
<link href="https://fonts.googleapis.com/css2?family=Carlito:ital,wght@0,400;0,700&display=swap" rel="stylesheet">
<style>
  :root {
    --brand-blue: #2f6ea8;
    --rule-blue: #4a7fb5;
    --ink: #1a1a1a;
    --muted-grey: #9a9a9a;
    --paper: #ffffff;
    --mist: #dfe9f3;
  }
  html, body {
    margin: 0;
    padding: 0;
    overflow: hidden;
    background: var(--paper);
  }
  .page {
    position: relative;
    width: 927px;
    height: 1200px;
    overflow: hidden;
    background: var(--paper);
    font-family: "Carlito", "Calibri", sans-serif;
    color: var(--ink);
  }
  .header-visual {
    position: absolute;
    top: 0;
    right: 0;
    width: 290px;
    height: 103px;
    background: linear-gradient(100deg, rgba(255,255,255,1) 0%, var(--mist) 55%, #eef3f8 100%);
  }
  .brand {
    position: absolute;
    top: 34px;
    left: 60px;
    display: flex;
    align-items: center;
    gap: 10px;
    font-size: 17px;
    font-weight: 700;
    color: var(--brand-blue);
  }
  .brand-dot {
    width: 18px;
    height: 18px;
    border-radius: 50%;
    background: var(--brand-blue);
  }
  .header-rule {
    position: absolute;
    top: 102px;
    left: 0;
    width: 927px;
    height: 2px;
    background: var(--rule-blue);
  }
  .section-tab {
    position: absolute;
    top: 103px;
    left: 455px;
    width: 472px;
    height: 42px;
    background: var(--brand-blue);
  }
  .section-tab svg { position: absolute; left: 0; top: 0; }
  .section-title {
    position: absolute;
    top: 2px;
    left: 36px;
    margin: 0;
    font-size: 31px;
    font-weight: 400;
    line-height: 40px;
    color: var(--paper);
    letter-spacing: 0.3px;
  }
  .content {
    position: absolute;
    top: 188px;
    left: 79px;
    width: 803px;
    font-size: 19.5px;
    line-height: 30px;
  }
  .content h2 {
    margin: 0 0 6px;
    text-align: center;
    font-size: 25px;
    font-weight: 700;
  }
  .content p {
    margin: 0;
    text-align: justify;
  }
  .conditions p { margin-top: 6px; }
  .content h3 {
    margin: 28px 0 4px;
    font-size: 27px;
    font-weight: 400;
    text-decoration: underline;
    text-underline-offset: 3px;
    text-decoration-thickness: 1px;
    line-height: 36px;
  }
  .footer-rule {
    position: absolute;
    top: 1156px;
    left: 0;
    width: 927px;
    height: 1px;
    background: var(--rule-blue);
    opacity: 0.7;
  }
  .folio {
    position: absolute;
    top: 1168px;
    right: 36px;
    font-size: 13px;
    color: var(--muted-grey);
    letter-spacing: 0.3px;
  }
</style>
</head>
<body>
<div class="page">
  <div class="header-visual" role="img" aria-label="Faint photograph of a pen resting on papers"></div>

  <div class="brand"><span class="brand-dot"></span>Redwell Institute Bayshore</div>

  <div class="header-rule"></div>
  <div class="section-tab">
    <svg width="30" height="42" viewBox="0 0 30 42" aria-hidden="true">
      <polygon points="0,0 30,0 30,42 14,42" fill="var(--paper)" opacity="0"/>
    </svg>
    <h1 class="section-title">GRADUATION REQUIREMENTS</h1>
  </div>

  <main class="content">
    <h2>Graduation Requirements</h2>
    <div class="conditions">
      <p style="margin-top:0">RWIB will confer the graduate degree or certificate when the student has met the following conditions:</p>
      <p>1. Earned an overall average GPA of 3.0 in all courses in the graduate or certificate program.</p>
      <p>2. Recommended by the faculty of the University.&nbsp; Student must have at least 2 instructor's recommendation.</p>
      <p>3. Certified by the Dean of the University Graduate School that all requirements of the degree or certificate being sought have been completed.</p>
    </div>

    <h3>Certificate Programs</h3>
    <p>Certificates require 15 credit hours for graduation.&nbsp; At least 9 of the credits must be in core courses taken by all individuals obtaining the same certificate.&nbsp; All the credits earned in a Certificate Programmay be used in a master's degree program provided a passing score.</p>

    <h3>Master of Business Administration Degree Program</h3>
    <p>Graduate Programs require 33 credit hours for graduation.&nbsp; At least 21 of the credits must be in core courses taken by all individuals obtaining the same degree.</p>
  </main>

  <div class="footer-rule"></div>
  <div class="folio">20::: REDWELL INSTITUTE</div>
</div>
</body>
</html>
```